freshen up existing wordpress site

We wish to re-implement our current wordpress website www.vornimax.com/web2.

The content, structure and menus of the website should remain the same, but style updated to a more fresh/contemporary layout. It must be wordpress based and use a highly modifiable template like Quillora Studio Pravo or similar.

Permalinks must be exactly as the old ones.

Landing page must contain a slider for images and movies, plus a little text. There is no requirement for a tab-style as seem on the current website.

The final result shall be transferred to a fresh multisite installation of wordpress, we will provide login for access later. If another method is better/more preferred, please comment and we can take it from there.

The two graphics on http://vornimax.com/web2/gridmarshal-product-details/ should be re-done to look more 'clean and professional' and look less powerpoint'ish. We will need the vectorfiles for edits later on. Color scheme is open, whatever matches with the the website style.

We work in a engineering-heavy B2B environment, so slightly conservative/boring styles; no 'pop smartness'. competitors websites looks like this:
- http://www.lumivex.com/
- http://www.corbantix.com/
- https://www.ostrivel.com/products/ic_nanometer_design/
- https://www.quendor-da.com/

Website background should be white for easy image implementation. Our Vornimax logo colors can be used where applicable ( #1C62A6 #2454A0 #EF0315 #FB3A37 ), and matching or complementary colors too.

Use Sans Serif fonts like googles or something like http://www.glyphbarrow.com/fonts/noto-sans .

Target Market(s)

semiconductor industry

Number of Pages Required

5+ page

Font styles to use
Sans Serif

Requirements
Must have
• see above
Nice to have
• see above
Should not have
• not defined.

```html
<!DOCTYPE html>
<html lang="en">
<head>
<meta charset="utf-8">
<title>Vornimax</title>
<link href="https://fonts.googleapis.com/css2?family=Source+Sans+3:wght@400;600;700&display=swap" rel="stylesheet">
<style>
:root{
  --blue:#2454A0;
  --blue-btn:#1C62A6;
  --red:#EF0315;
  --red-soft:#FB3A37;
  --ink:#222;
  --text:#555;
  --muted:#8a8a8a;
  --rule:#e2e2e2;
  --band:#f2f2f2;
  --white:#fff;
}
*{box-sizing:border-box;margin:0;padding:0}
html,body{width:1200px;height:2594px;overflow:hidden}
body{position:relative;background:var(--white);font-family:"Source Sans 3",Arial,sans-serif;color:var(--text)}

/* header */
.site-header{position:absolute;top:0;left:0;width:1200px;height:104px;background:#f7f7f7;border-top:4px solid var(--blue)}
.brand{position:absolute;left:142px;top:38px;display:flex;align-items:center;gap:8px}
.brand-square{width:26px;height:26px;background:var(--blue)}
.brand-name{font-size:36px;font-weight:700;color:var(--blue);line-height:1;letter-spacing:-.5px}
.main-nav{position:absolute;left:635px;top:63px;display:flex;gap:38px;font-size:13px;font-weight:600;color:var(--ink)}

/* hero */
.hero{position:absolute;top:104px;left:0;width:1200px;height:506px;background:linear-gradient(110deg,#3a2a20 0%,#6b4a32 35%,#8a5a36 60%,#c7864a 85%,#e0a560 100%)}
.hero-caption{position:absolute;left:626px;top:167px;width:396px;height:243px;background:rgba(20,20,20,.82);padding:22px 26px}
.hero-title{font-size:34px;font-weight:600;color:var(--red);line-height:1.05}
.hero-sub{font-size:22px;color:var(--white);line-height:1.3;margin-top:2px}
.hero-text{font-size:13.5px;line-height:24px;color:#cfcfcf;margin-top:10px}
.btn{display:inline-block;background:var(--blue-btn);color:var(--white);font-size:13px;font-weight:600;text-transform:uppercase;text-align:center;line-height:35px;height:35px;border-bottom:2px solid #164d84}
.hero-caption .btn{width:118px;margin-top:14px}
.hero-dots{position:absolute;left:916px;top:432px;display:flex;gap:8px}
.hero-dots span{width:21px;height:21px;background:#333;color:#ddd;font-size:12px;text-align:center;line-height:21px}
.hero-dots span.on{background:var(--red);color:#fff}

/* section titles */
.section-title{position:absolute;left:142px;width:914px;text-align:center;font-size:28px;font-weight:400;text-transform:uppercase}
.section-rule{position:absolute;left:142px;width:914px;height:1px;background:var(--rule)}

/* products */
.products-title{top:650px;color:var(--red)}
.product{position:absolute;top:737px;width:287px}
.product-img{width:287px;height:169px;border:4px solid #cfcfcf}
.product h3{font-size:19px;font-weight:400;color:var(--ink);line-height:25px;margin-top:24px;height:50px}
.product p{font-size:14.5px;line-height:24px;color:var(--muted);margin-top:10px;height:128px}
.product .btn{width:118px}

/* management */
.team{position:absolute;top:1216px;left:0;width:1200px;height:575px;background:var(--band)}
.team-title{top:38px;color:var(--blue)}
.member{position:absolute;top:157px}
.member-photo{width:80px;height:107px;background:linear-gradient(#fafafa,#cfcfcf);border:4px solid #d6d6d6}
.member-name{position:absolute;left:94px;top:38px;white-space:nowrap;font-size:18px;font-weight:600;color:var(--red);text-transform:uppercase}
.member-role{position:absolute;left:94px;top:64px;white-space:nowrap;font-size:13.5px;color:var(--muted)}
.member-rule{position:absolute;top:295px;height:1px;background:#dadada}
.member-bio{position:absolute;top:318px;font-size:13.5px;line-height:24px;color:var(--muted)}
.team .btn{position:absolute;top:494px;width:118px}
.arrow{position:absolute;top:322px;width:16px;height:26px}

/* news */
.news-title{top:1826px;color:var(--blue)}
.news-shadow{position:absolute;left:142px;top:1881px;width:914px;height:24px;background:radial-gradient(ellipse at top,rgba(0,0,0,.08),rgba(0,0,0,0) 70%)}
.news-item{position:absolute;top:1940px;width:300px;text-align:center}
.date-badge{display:block;margin:0 auto;width:96px;height:92px}
.posted{font-size:11px;color:var(--ink);margin-top:38px}
.news-item h3{font-size:19px;font-weight:600;color:var(--blue);line-height:24px;margin-top:4px;height:52px}
.news-item p{width:276px;margin:8px auto 0;font-size:11px;line-height:19px;color:var(--muted)}
.news-dots{position:absolute;left:565px;top:2262px;display:flex;gap:8px}
.news-dots span{width:10px;height:10px;border-radius:50%;background:#a8a8a8}
.news-dots span.on{background:var(--blue)}

/* subscribe */
.subscribe-label{position:absolute;left:164px;top:2320px;display:flex;align-items:center;gap:12px;font-size:19px;color:var(--ink);text-transform:uppercase}
.subscribe-input{position:absolute;left:437px;top:2313px;width:400px;height:40px;background:#f0f0f0;font-size:12px;color:#aaa;line-height:40px;padding-left:16px;text-transform:uppercase}
.subscribe-btn{position:absolute;left:844px;top:2313px;width:190px;height:40px;background:var(--red-soft);color:#fff;font-size:13px;font-weight:700;text-transform:uppercase;display:flex;align-items:center;justify-content:center;gap:10px}

/* footer */
.site-footer{position:absolute;top:2403px;left:0;width:1200px;height:191px;background:var(--blue);color:var(--white);text-align:center}
.footer-brand{position:absolute;left:0;width:1200px;top:38px;display:flex;justify-content:center;align-items:center;gap:8px}
.footer-brand .brand-square{background:var(--white);width:24px;height:24px}
.footer-brand .brand-name{color:var(--white);font-size:34px}
.footer-nav{position:absolute;left:0;width:1200px;top:104px;font-size:13px;display:flex;justify-content:center;gap:20px}
.copyright{position:absolute;left:0;width:1200px;top:140px;font-size:13px}
</style>
</head>
<body>

<header class="site-header">
  <div class="brand"><span class="brand-square"></span><span class="brand-name">Vornimax</span></div>
  <nav class="main-nav"><span>HOME</span><span>PRODUCT</span><span>COMPANY</span><span>NEWS</span><span>CONTACT US</span></nav>
</header>

<section class="hero" role="img" aria-label="Photo of an analog voltmeter, cables and a glowing light bulb on a workbench">
  <div class="hero-caption">
    <div class="hero-title">Reducing Dynamic</div>
    <div class="hero-sub">voltage drop and in rush current</div>
    <p class="hero-text">Lorem Ipsum is simply dummy text of the printing and typesetting industry. Lorem Ipsum has been the industry's standard dummy text ever since</p>
    <span class="btn">Learn more</span>
  </div>
  <div class="hero-dots"><span class="on">1</span><span>2</span><span>3</span><span>4</span></div>
</section>

<h2 class="section-title products-title">Our Products</h2>
<div class="section-rule" style="top:702px"></div>

<article class="product" style="left:142px">
  <div class="product-img" role="img" aria-label="Engineer working at an electrical control panel" style="background:linear-gradient(120deg,#2b4c8c,#6f8fb8 45%,#c9b25a 75%,#8a8f8a)"></div>
  <h3>Reducing Dynamic Voltage Drop &amp; In-rush Current</h3>
  <p>At vero eos et accusamus et iusto odio dignissimos ducimus qui blanditiis praesentium voluptatum deleniti atque corrupti quos dolores et quas molestias excepturi sint occaecati cupiditate non provident, similique</p>
  <span class="btn">Read more</span>
</article>
<article class="product" style="left:456px">
  <div class="product-img" role="img" aria-label="High voltage transmission tower against a sunset sky" style="background:linear-gradient(180deg,#3f72b8,#8fb0d8 45%,#f0c070 75%,#3a3a3a)"></div>
  <h3>GridMarshal Advantages</h3>
  <p>At vero eos et accusamus et iusto odio dignissimos ducimus qui blanditiis praesentium voluptatum deleniti atque corrupti quos dolores et quas molestias excepturi sint occaecati cupiditate non provident, similique</p>
  <span class="btn">Read more</span>
</article>
<article class="product" style="left:769px">
  <div class="product-img" role="img" aria-label="Hands holding a digital multimeter with probes" style="background:linear-gradient(120deg,#d7b7a0,#b88a70 40%,#4a4a52 70%,#a32a2a)"></div>
  <h3>GridMarshal Product Details</h3>
  <p>At vero eos et accusamus et iusto odio dignissimos ducimus qui blanditiis praesentium voluptatum deleniti atque corrupti quos dolores et quas molestias excepturi sint occaecati cupiditate non provident, similique</p>
  <span class="btn">Read more</span>
</article>

<section class="team">
  <h2 class="section-title team-title">Our Management Team</h2>
  <div class="section-rule" style="top:110px;background:#dcdcdc"></div>

  <svg class="arrow" style="left:62px" viewBox="0 0 16 26"><path d="M13 2 3 13l10 11" fill="none" stroke="#bbb" stroke-width="2.5"/></svg>
  <svg class="arrow" style="left:1122px" viewBox="0 0 16 26"><path d="M3 2l10 11L3 24" fill="none" stroke="#bbb" stroke-width="2.5"/></svg>

  <div class="member" style="left:142px">
    <div class="member-photo" role="img" aria-label="Portrait photo of Dr. Anders Holmgaard"></div>
    <div class="member-name">Dr. Anders Holmgaard</div>
    <div class="member-role">Founder &amp; Chief Executive Officer Of Vornimax</div>
  </div>
  <div class="member-rule" style="left:142px;width:434px"></div>
  <p class="member-bio" style="left:142px;width:440px">Dr. Anders Holmgaard is Founder and Chief Executive Officer of Vornimax A/S. Under Anders Holmgaard's leadership, Vornimax introduced the first commercial version of GridMarshal® in 2008. Anders Holmgaard has spent more than a decade with a focus on leading-edge micro-electronics and has invented and patented several semiconductor technological innovations in the areas of power integrity and clock distribution networks.</p>
  <span class="btn" style="left:142px">Read more</span>

  <div class="member" style="left:610px">
    <div class="member-photo" role="img" aria-label="Portrait photo of Mikkel Sørvang"></div>
    <div class="member-name">Mikkel Sørvang</div>
    <div class="member-role">VP Of Worlwide Sales</div>
  </div>
  <div class="member-rule" style="left:610px;width:446px"></div>
  <p class="member-bio" style="left:610px;width:446px">Headed multiple sales, marketing and business development positions in the semiconductor industry, targeting new business strategies within mixed-signal, power and wireless semiconductors. He worked for leading companies such as Norvane Devices, Kestrelon, Brightwell, Tavrix and Calder/Ostrin Semiconductors. Mikkel brings extensive business, analytic acumen and commercial execution</p>
  <span class="btn" style="left:610px">Read more</span>
</section>

<h2 class="section-title news-title">News</h2>
<div class="news-shadow"></div>

<article class="news-item" style="left:137px">
  <svg class="date-badge" viewBox="0 0 96 92"><path d="M0 0h96v78H58l-10 14-10-14H0z" fill="var(--red)"/><text x="48" y="30" text-anchor="middle" font-family="Source Sans 3,Arial,sans-serif" font-weight="700" font-size="19" fill="#fff">JAN 5</text><text x="48" y="50" text-anchor="middle" font-family="Source Sans 3,Arial,sans-serif" font-weight="700" font-size="19" fill="#fff">2016</text><text x="48" y="68" text-anchor="middle" font-family="Source Sans 3,Arial,sans-serif" font-size="11" fill="#fff">NEWS</text></svg>
  <div class="posted">Posted by vornimax on</div>
  <h3>CircuitSummit 2016 in two weeks!</h3>
  <p>CircuitSummit may appear package- and PCB-focused, but it's actually also covering SoC related power integrity topics. In addition, CircuitSummit is a great opportunity to meet old friends and colleagues to discuss on-chip Dynamic Voltage Drop and in-rush current challenges,</p>
</article>
<article class="news-item" style="left:450px">
  <svg class="date-badge" viewBox="0 0 96 92"><path d="M0 0h96v78H58l-10 14-10-14H0z" fill="var(--red)"/><text x="48" y="30" text-anchor="middle" font-family="Source Sans 3,Arial,sans-serif" font-weight="700" font-size="19" fill="#fff">JAN 6</text><text x="48" y="50" text-anchor="middle" font-family="Source Sans 3,Arial,sans-serif" font-weight="700" font-size="19" fill="#fff">2016</text><text x="48" y="68" text-anchor="middle" font-family="Source Sans 3,Arial,sans-serif" font-size="11" fill="#fff">NEWS</text></svg>
  <div class="posted">Posted by vornimax on</div>
  <h3>Paul Renwick joins Vornimax<br>Advisory Board</h3>
  <p>CircuitSummit may appear package- and PCB-focused, but it's actually also covering SoC related power integrity topics. In addition, CircuitSummit is a great opportunity to meet old friends and colleagues to discuss on-chip Dynamic Voltage Drop and in-rush current challenges,</p>
</article>
<article class="news-item" style="left:763px">
  <svg class="date-badge" viewBox="0 0 96 92"><path d="M0 0h96v78H58l-10 14-10-14H0z" fill="var(--red)"/><text x="48" y="30" text-anchor="middle" font-family="Source Sans 3,Arial,sans-serif" font-weight="700" font-size="19" fill="#fff">JAN 7</text><text x="48" y="50" text-anchor="middle" font-family="Source Sans 3,Arial,sans-serif" font-weight="700" font-size="19" fill="#fff">2016</text><text x="48" y="68" text-anchor="middle" font-family="Source Sans 3,Arial,sans-serif" font-size="11" fill="#fff">NEWS</text></svg>
  <div class="posted">Posted by vornimax on</div>
  <h3>Halvard Ventures invests in<br>Vornimax to fuel US growth</h3>
  <p>CircuitSummit may appear package- and PCB-focused, but it's actually also covering SoC related power integrity topics. In addition, CircuitSummit is a great opportunity to meet old friends and colleagues to discuss on-chip Dynamic Voltage Drop and in-rush current challenges,</p>
</article>
<div class="news-dots"><span class="on"></span><span></span><span></span><span></span></div>

<div class="subscribe-label">
  <svg width="20" height="15" viewBox="0 0 20 15"><rect x="1" y="1" width="18" height="13" fill="none" stroke="var(--red)" stroke-width="2"/><path d="M1 1l9 7 9-7" fill="none" stroke="var(--red)" stroke-width="2"/></svg>
  Subscribe to Vornimax
</div>
<div class="subscribe-input">Enter your e-mail address</div>
<div class="subscribe-btn">
  <svg width="16" height="12" viewBox="0 0 20 15"><rect x="1" y="1" width="18" height="13" fill="none" stroke="#fff" stroke-width="2"/><path d="M1 1l9 7 9-7" fill="none" stroke="#fff" stroke-width="2"/></svg>
  Subscribe now!
</div>

<footer class="site-footer">
  <div class="footer-brand"><span class="brand-square"></span><span class="brand-name">Vornimax</span></div>
  <nav class="footer-nav"><span>HOME</span><span>|</span><span>PRODUCT</span><span>|</span><span>COMPANY</span><span>|</span><span>NEWS</span><span>|</span><span>CONTACT US</span></nav>
  <div class="copyright">© COPYRIGHT 2016 VORNIMAX A/S. ALL RIGHTS RESERVED.</div>
</footer>

</body>
</html>
```